Harborline Auto LLC

Car Dealer Customer Service
Address: 2874 Cresthaven Road, Shelbyville, TN 37162
web: www.harborlineautoxq.net
email: harborlineautoxq@mailnest.example
Phone: (931) 555-0148
Phone: (629) 555-0173

```html
<!DOCTYPE html>
<html lang="en">
<head>
<meta charset="utf-8">
<title>Harborline Auto – Business Card</title>
<link rel="stylesheet" href="https://fonts.googleapis.com/css2?family=Montserrat:wght@700;800&family=Arimo:wght@400&family=Bebas+Neue&display=swap">
<style>
  :root {
    --backdrop: #141416;
    --card: #28292c;
    --card-back: #2c2d30;
    --gold: #e8b13a;
    --blue: #2a8fce;
    --white: #f2f2f2;
    --muted-mark: #4a4b4f;
  }
  * { margin: 0; padding: 0; box-sizing: border-box; }
  html, body {
    width: 1200px; height: 820px; overflow: hidden;
    background: var(--backdrop);
  }
  .sheet {
    width: 1200px; height: 820px;
    display: flex; flex-direction: column;
    align-items: center; justify-content: center; gap: 40px;
  }
  .card {
    position: relative;
    width: 620px; height: 354px;
    border: 3px solid var(--gold);
    overflow: hidden;
  }
  .card--front { background: var(--card); }
  .card--back { background: var(--card-back); }

  /* Front */
  .brand {
    position: absolute; left: 290px; top: 70px;
    display: flex; align-items: center; gap: 14px;
  }
  .brand__dot {
    width: 46px; height: 46px; border-radius: 50%;
    background: var(--blue);
  }
  .brand__name {
    font-family: "Montserrat", sans-serif; font-weight: 800;
    font-size: 30px; letter-spacing: 1px; color: var(--blue);
    line-height: 1;
  }
  .divider {
    position: absolute; left: 40px; top: 178px;
    width: 545px; height: 1px; background: var(--gold);
  }
  .person { position: absolute; left: 40px; top: 148px; }
  .person__name {
    font-family: "Montserrat", sans-serif; font-weight: 800;
    font-size: 21px; color: var(--blue); line-height: 1;
  }
  .person__title {
    margin-top: 10px;
    font-family: "Arimo", sans-serif; font-size: 17px; color: var(--white);
  }
  .contact-rule {
    position: absolute; left: 40px; top: 226px;
    width: 230px; height: 1px; background: var(--gold);
  }
  .contacts {
    position: absolute; left: 40px; top: 238px;
    list-style: none;
    font-family: "Arimo", sans-serif; font-size: 16px; color: var(--white);
  }
  .contacts li {
    display: flex; align-items: center; gap: 10px; height: 23px;
  }
  .contacts svg { width: 15px; height: 15px; flex: none; }
  .contacts .accent { color: var(--blue); }
  .address {
    position: absolute; right: 40px; top: 196px;
    font-family: "Arimo", sans-serif; font-size: 16px;
    color: var(--white); line-height: 1.35; text-align: left;
  }

  /* Back */
  .services {
    position: absolute; right: 40px; top: 34px;
    font-family: "Bebas Neue", sans-serif; font-size: 38px;
    color: var(--blue); line-height: 0.95; text-align: right;
  }
  .services span { display: block; }
  .services span:nth-child(1) { margin-right: 50px; }
  .services span:nth-child(2) { margin-right: 25px; }
  .back-mark {
    position: absolute; left: 60px; top: 175px;
    display: flex; align-items: center; gap: 18px;
  }
  .back-mark__dot {
    width: 64px; height: 64px; border-radius: 50%;
    background: var(--muted-mark);
  }
  .back-mark__name {
    font-family: "Montserrat", sans-serif; font-weight: 800;
    font-size: 38px; color: var(--muted-mark); letter-spacing: 1px;
  }
</style>
</head>
<body>
<main class="sheet">
  <section class="card card--front">
    <div class="brand">
      <span class="brand__dot"></span>
      <span class="brand__name">HARBORLINE AUTO</span>
    </div>

    <div class="person">
      <div class="person__name">DANIEL MERCER</div>
    </div>
    <div class="divider"></div>
    <div class="person__title" style="position:absolute;left:40px;top:188px;">Managing Director</div>

    <div class="contact-rule"></div>
    <ul class="contacts">
      <li>
        <svg viewBox="0 0 16 16" aria-hidden="true"><path d="M3 1.5l3 3-1.6 1.8a9 9 0 0 0 5.3 5.3L11.5 10l3 3-1.8 2A12 12 0 0 1 1 3.3z" fill="var(--blue)"/></svg>
        (931) 555-0148
      </li>
      <li>
        <svg viewBox="0 0 16 16" aria-hidden="true"><path d="M3 1.5l3 3-1.6 1.8a9 9 0 0 0 5.3 5.3L11.5 10l3 3-1.8 2A12 12 0 0 1 1 3.3z" fill="var(--blue)"/></svg>
        (629) 555-0173
      </li>
      <li>
        <svg viewBox="0 0 16 16" aria-hidden="true"><g fill="none" stroke="var(--blue)" stroke-width="1.4"><circle cx="8" cy="8" r="6.5"/><ellipse cx="8" cy="8" rx="3" ry="6.5"/><path d="M1.5 8h13M2.5 4.8h11M2.5 11.2h11"/></g></svg>
        <span>www.<span class="accent">harborlineautoxq</span>.net</span>
      </li>
      <li>
        <svg viewBox="0 0 16 16" aria-hidden="true"><rect x="1" y="3.5" width="14" height="9" fill="var(--blue)"/><path d="M1 3.5l7 5.5 7-5.5" fill="none" stroke="var(--card)" stroke-width="1.2"/></svg>
        harborlineautoxq@mailnest.example
      </li>
    </ul>

    <address class="address" style="font-style:normal;">
      2874 Cresthaven Road<br>
      Shelbyville, TN 37162
    </address>
  </section>

  <section class="card card--back">
    <div class="back-mark">
      <span class="back-mark__dot"></span>
      <span class="back-mark__name">HARBORLINE AUTO</span>
    </div>
    <div class="services">
      <span>Car Dealer</span>
      <span>Customer</span>
      <span>Service</span>
    </div>
  </section>
</main>
</body>
</html>
```